Re-design and craft the perfect CV platform

We are building a CV-based platform designed to connect employees and employers, with a strong focus on individual users. As we're just starting out, we're looking to have our platform and logo redesigned to better reflect our vision
https://app.zelvorhire.com/
Colors like in the logo attached
#87C032 #6A6E71 #618930 - also you can add more colors if you like.
https://app.zelvorhire.com/dashboard - This page would be nice if you plan it, like personal Bio dashboard. Attached picture (Dashboard wanted) one idea from how we would like to be, but we are open for new professional ideas/solutions.
https://app.zelvorhire.com/posts - On this page we want to be showed the jobs posted. Attached one picture about our idea (jobs page wanted)
https://app.zelvorhire.com/profile - design something nice.
Only Photoshop, Illustrator or Figma
Other pictures from the app attached (as looking right now)

Target Market(s)

Job seekers, HR, Recruiters

Industry/Entity Type

HR Tech

Number of Pages Required

5+ page

Colors
00AB8E
00BBA5
67D7C9
C6EFE9
E9F9F6

```html
<!DOCTYPE html>
<html lang="en">
<head>
<meta charset="UTF-8">
<title>Zelvorhire – Recruitment Web App Access</title>
<link href="https://fonts.googleapis.com/css2?family=Poppins:wght@300;400;500;600;700&display=swap" rel="stylesheet">
<style>
  :root {
    --green: #87C032;
    --green-dark: #618930;
    --grey: #6A6E71;
    --text: #4f5457;
    --field: #F0F0F1;
    --divider: #E3E5E8;
    --bg-top: #F4F6F8;
    --bg-bottom: #FFFFFF;
  }
  * { box-sizing: border-box; margin: 0; padding: 0; }
  html, body { width: 1200px; height: 712px; overflow: hidden; }
  body {
    font-family: "Poppins", sans-serif;
    background: linear-gradient(180deg, var(--bg-top) 0%, var(--bg-bottom) 40%, var(--bg-top) 100%);
    position: relative;
    color: var(--text);
  }
  .brand {
    position: absolute;
    left: 111px; width: 371px;
    top: 112px;
    text-align: center;
    font-size: 34px;
    font-weight: 600;
    color: var(--green);
    letter-spacing: 0.5px;
  }
  .login-card {
    position: absolute;
    left: 111px; top: 216px;
    width: 372px; height: 380px;
    background: #fff;
    border: 1px solid var(--green);
    border-radius: 30px;
    box-shadow: 0 26px 40px -22px rgba(60, 70, 80, 0.22);
    padding: 0 33px 0 33px;
  }
  .card-title {
    position: absolute; left: 32px; top: 24px;
    font-size: 19.5px; font-weight: 600; color: var(--grey);
  }
  .card-title .accent { color: var(--green); }
  .card-divider {
    position: absolute; left: 28px; right: 28px; top: 70px;
    border-top: 1px solid var(--divider);
  }
  .login-heading {
    position: absolute; left: 32px; top: 106px;
    font-size: 15px; font-weight: 500; color: var(--grey);
  }
  .login-intro {
    position: absolute; left: 32px; top: 138px; width: 320px;
    font-size: 11.3px; font-weight: 300; line-height: 16.5px; color: var(--text);
  }
  .field-label {
    position: absolute; left: 32px; top: 204px;
    font-size: 10.5px; font-weight: 600; color: var(--text);
  }
  .field-label .required { color: var(--green); }
  .email-field {
    position: absolute; left: 33px; top: 226px;
    width: 304px; height: 44px;
    background: var(--field);
    border-radius: 22px;
    display: flex; align-items: center;
    padding-left: 21px;
    font-size: 10.5px; font-weight: 300; color: var(--text);
  }
  .email-field svg { margin-right: 10px; }
  .continue-button {
    position: absolute; left: 33px; top: 287px;
    width: 304px; height: 44px;
    background: var(--green);
    border-radius: 22px;
    display: flex; align-items: center; justify-content: center;
    font-size: 11.5px; font-weight: 700; color: #fff; letter-spacing: 0.2px;
  }
  .continue-arrow {
    position: absolute; right: 6px; top: 5.5px;
    width: 33px; height: 33px; border-radius: 50%;
    background: #fff;
    display: flex; align-items: center; justify-content: center;
  }
  .hero-photo {
    position: absolute;
    left: 525px; top: 150px;
    width: 675px; height: 562px;
    border-radius: 260px 0 0 0;
    background:
      radial-gradient(ellipse at 82% 70%, rgba(135, 192, 50, 0.85) 0%, rgba(135, 192, 50, 0.3) 45%, rgba(135, 192, 50, 0) 70%),
      linear-gradient(160deg, #EEF1F3 0%, #B9C3CC 45%, #6C8BAF 100%);
  }
</style>
</head>
<body>
  <div class="brand">Zelvorhire</div>

  <section class="login-card">
    <h1 class="card-title">Recruitment <span class="accent">Web App</span> Access</h1>
    <div class="card-divider"></div>
    <h2 class="login-heading">Log in to your account</h2>
    <p class="login-intro">Welcome to Alex Marlow, please put your login credentials below to start using the app</p>
    <label class="field-label">Email Address<span class="required">*</span></label>
    <div class="email-field">
      <svg width="11" height="9" viewBox="0 0 11 9"><rect x="0" y="0" width="11" height="9" rx="1.2" fill="#5c6164"/><path d="M0.8 1.2 L5.5 4.8 L10.2 1.2" stroke="#F0F0F1" stroke-width="1" fill="none"/></svg>
      Enter email address
    </div>
    <div class="continue-button">CONTINUE
      <span class="continue-arrow"><svg width="7" height="9" viewBox="0 0 7 9"><path d="M2 1 L5 4.5 L2 8" stroke="#4f5457" stroke-width="1.2" fill="none"/></svg></span>
    </div>
  </section>

  <div class="hero-photo" role="img" aria-label="Photo of a man in glasses and a grey sweater sitting on a lime green bean bag, working on a silver laptop"></div>
</body>
</html>
```